Classy, Elegant, Simple Business Card Design

Looking to have a classy, simple, and elegant design. Want a top notch designed business card. I really like the look of the new torvane credit card. I also like the design I attached. I am trying to reach 21-29 year old females for booking us for there wedding or event. We offer Disc Jockey Service, Photo Booth Rentals, and Uplighting .

Target Market(s)

21-28 year old females

Contact Information for Business Card

Has to have logo, website, email, and phone number

Font styles to use
Other font styles liked:
• open to font choice, modern, clean
Designer to choose
33a6d7
0791cd
0555a3
ffffff

Requirements
Must have
• Has to have logo, website, email, and phone number
Nice to have
• I really like the design of the new torvane credit card. I also included my logo and some designs I like
Should not have
• clutter or too much info

```html
<!DOCTYPE html>
<html lang="en">
<head>
<meta charset="utf-8">
<title>Tidecrest Event Group – Business Card</title>
<link href="https://fonts.googleapis.com/css2?family=Lato:wght@400;700&display=swap" rel="stylesheet">
<style>
  :root {
    --stage: #d4d4d4;
    --navy: #1460a0;
    --sky: #33a6d7;
    --bright: #0791cd;
    --royal: #0555a3;
    --white: #ffffff;
    --paper: #f7f7f7;
    --grey: #8a8f96;
  }
  * { margin: 0; padding: 0; box-sizing: border-box; }
  html, body { width: 1200px; height: 802px; overflow: hidden; }
  body {
    background: var(--stage);
    position: relative;
    font-family: "Lato", sans-serif;
  }
  .card {
    position: absolute;
    top: 274px;
    width: 442px;
    height: 264px;
    overflow: hidden;
    box-shadow: 0 3px 8px rgba(0,0,0,0.25);
  }
  .card--front { left: 136px; background: var(--navy); }
  .card--back { left: 624px; background: var(--paper); }

  .front-accent {
    position: absolute;
    right: 0; top: 0;
    width: 270px; height: 264px;
    background: radial-gradient(ellipse at 75% 60%, var(--bright) 0%, rgba(7,145,205,0.55) 45%, rgba(20,96,160,0) 75%);
  }

  .contact-list {
    position: absolute;
    left: 20px; top: 60px;
    list-style: none;
    color: var(--white);
    font-size: 15px;
    line-height: 20px;
  }
  .contact-list li { display: flex; align-items: center; gap: 4px; white-space: nowrap; }
  .contact-list svg { width: 16px; height: 16px; flex: none; }

  .service-list {
    position: absolute;
    left: 23px; top: 146px;
    list-style: none;
    color: var(--white);
    font-size: 15px;
    line-height: 19.5px;
  }
  .service-list li::before {
    content: "";
    display: inline-block;
    width: 7px; height: 7px;
    border-radius: 50%;
    background: var(--white);
    margin-right: 5px;
    vertical-align: 2px;
  }

  .brand {
    position: absolute;
    left: 0; right: 0;
    top: 158px;
    text-align: center;
  }
  .brand-name {
    font-size: 30px;
    font-weight: 400;
    letter-spacing: 2px;
    color: var(--royal);
    line-height: 1;
  }
  .brand-tagline {
    margin-top: 4px;
    font-size: 11px;
    letter-spacing: 6px;
    color: var(--grey);
    padding-left: 6px;
  }
</style>
</head>
<body>
  <section class="card card--front" aria-label="Card front">
    <div class="front-accent" role="img" aria-label="Large decorative monogram in light blue tones"></div>
    <ul class="contact-list">
      <li>
        <svg viewBox="0 0 16 16" aria-hidden="true"><circle cx="8" cy="8" r="7.5" fill="#fff"/><path d="M5 5.5c0-.6.5-1 1-1h.6l.8 1.8-.8.7c.4.9 1.1 1.6 2 2l.7-.8 1.8.8v.6c0 .5-.4 1-1 1C7.5 10.6 5 8.1 5 5.5z" fill="#1460a0"/></svg>
        044-555 018 274
      </li>
      <li>
        <svg viewBox="0 0 16 16" aria-hidden="true"><circle cx="8" cy="8" r="7.5" fill="#fff"/><rect x="4.2" y="5.3" width="7.6" height="5.4" fill="none" stroke="#1460a0" stroke-width="1.1"/><path d="M4.3 5.5 8 8.4l3.7-2.9" fill="none" stroke="#1460a0" stroke-width="1.1"/></svg>
        hello@tidecrest.com
      </li>
      <li>
        <svg viewBox="0 0 16 16" aria-hidden="true"><circle cx="8" cy="8" r="7.5" fill="#fff"/><circle cx="8" cy="8" r="3.6" fill="none" stroke="#1460a0" stroke-width="1.1"/><path d="M4.4 8h7.2M8 4.4c-1.4 1.8-1.4 5.4 0 7.2M8 4.4c1.4 1.8 1.4 5.4 0 7.2" fill="none" stroke="#1460a0" stroke-width="0.9"/></svg>
        www.tidecrest.com
      </li>
    </ul>
    <ul class="service-list">
      <li>Disc Jockey Service</li>
      <li>Photo Booth Rentals</li>
      <li>Uplighting</li>
    </ul>
  </section>

  <section class="card card--back" aria-label="Card back">
    <div class="brand">
      <div class="brand-name">TIDECREST</div>
      <div class="brand-tagline">EVENT GROUP</div>
    </div>
  </section>
</body>
</html>
```